Basic Commercial & Residential Real Estate Web Site

I need a basic website for a new real estate company that deals with both residential and commercial sales. It must be clean and professional. We sell homes, office buildings, farms, and ranches. It should feel crisp and clean.
I need a main page with my logo and links to commercial, residential, farm and land searches with contact data forms. Also incorporated would be a mls property search (IDX) form. I am in Northern California and the current site I posted is at www.tlvarden.com. I need the functionality of the links and the supporting pages. I do not have all the copy ready because I did not know what to expect.
Updates

Project Deadline Extended
Reason: I apologize, I am extremely busy and you all need more data to do a good job. All the designs are great so far and it is extremely difficult to choose at this point. I haven't given you enough data. I haver now uploaded some relevent photos (not very good) and edited the brief. I am looking for what I call the Landing or main page with some functionality built in to other pages which I also need. Example if you click on "Commercial" it should go to a page that discusses our commercial dept.......

I would like to thank all the designers for all their hard work and efforts, I wish I could reward you all.

Thanks again for your creative and professional designs.

Edwin

Target Market(s)

Corporate Execs for the Commercial Buildings
Homeowners/Families for the Homes and Farms
Upper end people for the land to build estates

Industry/Entity Type

Real Estate

Font styles to use
Sans Serif

Requirements
Must have
• Our Logo should be prominent, pronounced
Need contact data or button
Functional Page that links to other data pages
Must Have a "search for properties" feature
Must say "Commercial and Residential Representation"
Pictures of Commercial Building and Nice Home (Tradtional not contemporary)
Nice to have
• Individual Buttons or links to "Commercial, Residential, Farm/Ranch, Land"
Contact Data displayed
button that says "Maple Crest"-next to button is Maple Crest Logo-see www.maplecrest.bz
Links to "Buyers and "Sellers"
Links to Facebook, twitter,.....etc
Should not have
• 20+ story commercial buildings or ultra modern. See uploaded files of typical buildings for commercial.

```html
<!DOCTYPE html>
<html lang="en">
<head>
<meta charset="utf-8">
<title>Properties by Varden</title>
<link href="https://fonts.googleapis.com/css2?family=Open+Sans:wght@400;600&family=Questrial&display=swap" rel="stylesheet">
<style>
:root{
  --dark:#2a2a2a;
  --footer:#252525;
  --blue:#2ba6de;
  --btn-top:#4cc0ee;
  --btn-bottom:#1b9ad6;
  --text:#6f6f6f;
  --muted:#9a9a9a;
  --heading:#222;
  --line:#dcdcdc;
}
*{margin:0;padding:0;box-sizing:border-box}
html,body{width:746px;height:1200px;overflow:hidden;background:#fff}
body{font-family:"Open Sans",sans-serif;color:var(--text);position:relative}
.site-header{position:absolute;left:0;top:0;width:746px;height:86px;background:var(--dark)}
.brand{position:absolute;left:54px;top:22px;display:flex;align-items:center;gap:8px}
.brand-mark{width:12px;height:12px;border-radius:50%;background:#fff}
.brand-name{font-family:"Questrial",sans-serif;color:#fff;font-size:22px;letter-spacing:1px;line-height:1.1}
.social-top{position:absolute;right:60px;top:22px;display:flex;gap:6px}
.social-top span{width:14px;height:14px;border-radius:50%;background:#fff;display:block}
.main-nav{position:absolute;right:62px;top:51px;display:flex;font-size:11px;color:#fff;text-transform:uppercase}
.main-nav a{color:#fff;text-decoration:none;padding:0 11px;border-left:1px solid #666;line-height:14px}
.main-nav a:first-child{border-left:0;color:var(--blue)}
.main-nav a:last-child{padding-right:0}
.hero{position:absolute;left:0;top:86px;width:746px;height:304px;background:linear-gradient(135deg,#6b5d52 0%,#c7c2ba 35%,#e8e6e0 55%,#a59b90 80%,#4a4440 100%)}
.hero-title{position:absolute;top:110px;width:100%;text-align:center;color:#fff;font-size:24px;font-weight:600;text-shadow:0 1px 3px rgba(0,0,0,.5);letter-spacing:.3px}
.hero-sub{position:absolute;top:146px;width:100%;text-align:center;color:#fff;font-size:18px;text-shadow:0 1px 3px rgba(0,0,0,.5)}
.hero-dots{position:absolute;top:283px;left:348px;display:flex;gap:3px}
.hero-dots span{width:9px;height:9px;border-radius:50%;background:rgba(255,255,255,.45)}
.hero-dots span:first-child{background:#fff}
.welcome{position:absolute;top:418px;left:60px;width:626px;text-align:center}
.welcome h1{font-family:"Questrial",sans-serif;font-weight:400;font-size:23px;color:var(--heading)}
.welcome p{font-size:8.6px;line-height:15px;margin-top:6px}
.cards{position:absolute;top:518px;left:63px;display:flex;gap:11px}
.card{width:200px;height:200px;border:1px solid var(--line);text-align:center}
.card-photo{height:91px}
.card h2{font-family:"Open Sans",sans-serif;font-weight:400;font-size:15px;color:var(--heading);margin-top:10px}
.card p{font-size:8px;line-height:12.5px;color:var(--muted);padding:0 17px;margin-top:3px}
.btn{display:inline-block;margin-top:6px;width:71px;height:21px;line-height:21px;font-size:8px;color:#fff;background:linear-gradient(var(--btn-top),var(--btn-bottom));border-radius:2px;text-transform:uppercase}
.divider-soft{position:absolute;top:742px;left:20px;width:706px;height:8px;background:radial-gradient(ellipse at center top,rgba(0,0,0,.05),transparent 70%)}
.about{position:absolute;top:770px;left:52px;width:384px}
.about h2{font-family:"Open Sans",sans-serif;font-weight:400;font-size:19px;color:var(--heading)}
.about .lead{font-size:10px;line-height:14px;margin-top:7px}
.about p{font-size:8px;line-height:14px;margin-top:9px}
.gallery{position:absolute;top:760px;left:465px;width:230px;height:182px;border:1px solid var(--line);background:linear-gradient(#fff 70%,#f1f1f1)}
.gallery h3{font-family:"Questrial",sans-serif;font-weight:400;font-size:15px;color:var(--blue);position:absolute;left:17px;top:14px}
.thumbs{position:absolute;left:17px;top:42px;display:grid;grid-template-columns:repeat(3,58px);gap:11px 11px}
.thumb{width:58px;height:54px;background:#fff;box-shadow:0 0 2px rgba(0,0,0,.25);padding:3px}
.thumb div{width:100%;height:100%}
.footer{position:absolute;top:982px;left:0;width:746px;height:218px;background:var(--footer)}
.footer-stripe{position:absolute;top:0;left:0;width:100%;height:6px;background:repeating-linear-gradient(45deg,#9a9a9a 0 1px,#d6d6d6 1px 3px)}
.footer-col{position:absolute;top:31px}
.footer-col h4{font-weight:400;font-size:12.5px;color:#fff;margin-bottom:6px}
.footer-col a{display:block;font-size:8px;color:#e5e5e5;text-decoration:none;line-height:16px}
.footer-social{display:flex;gap:6px;margin-top:4px}
.footer-social span{width:15px;height:15px;background:#555;border-radius:2px}
.footer-rule{position:absolute;top:166px;left:52px;width:642px;height:1px;background:#3a3a3a}
.copyright{position:absolute;top:180px;left:59px;font-size:8px;color:#888}
</style>
</head>
<body>
<header class="site-header">
  <div class="brand"><span class="brand-mark"></span><span class="brand-name">PROPERTIES BY VARDEN</span></div>
  <div class="social-top" aria-label="Social links"><span></span><span></span><span></span></div>
  <nav class="main-nav">
    <a href="#">Home</a><a href="#">Commercial</a><a href="#">Residential</a><a href="#">Farm</a><a href="#">Vacant Land</a><a href="#">Contact</a>
  </nav>
</header>

<section class="hero" role="img" aria-label="Bright modern kitchen and dining room with large windows">
  <div class="hero-title">WE SELL LUXURY HOME, BUILDING &amp; FRAMS</div>
  <div class="hero-sub">PHASELLUS FELIS DOLOR SCELERISQUE</div>
  <div class="hero-dots"><span></span><span></span><span></span><span></span></div>
</section>

<section class="welcome">
  <h1>Welcome to Properties by Varden homepage</h1>
  <p>Phasellus felis dolor scelerisque a tempus eget lobortis id libero Aliquam nec erat at purus cursus interdum Vestibulum ligula augue bibendum accumsan vestibulum ut commodo a mi Morbi ornare gravida elit Integer congue augue et malesuada iaculis ipsum dui aliquet felis at cursus magna nisl nec elit Vestibulum gravida Praesent elementum elit at tellus Malesuada nec ultricies sit amet porttitor</p>
</section>

<section class="cards">
  <article class="card">
    <div class="card-photo" role="img" aria-label="White luxury home kitchen" style="background:linear-gradient(135deg,#d9d4cc,#f3f1ec 50%,#8a7f74)"></div>
    <h2>Luxury Home</h2>
    <p>Mauris neque metus malesuada nec ultri-cies sit amet porttitor mattis enim. In massa libero interdum nec</p>
    <a class="btn">View More</a>
  </article>
  <article class="card">
    <div class="card-photo" role="img" aria-label="Glass office buildings against blue sky" style="background:linear-gradient(160deg,#9cc4e4,#2f6f9e 55%,#1c3f5e)"></div>
    <h2>Office Buildings</h2>
    <p>Mauris neque metus malesuada nec ultri-cies sit amet porttitor mattis enim. In massa libero interdum nec</p>
    <a class="btn">View More</a>
  </article>
  <article class="card">
    <div class="card-photo" role="img" aria-label="Rolling farmland with trees" style="background:linear-gradient(#c9cdc4,#7f8a4c 40%,#c39a5a 75%,#a7783c)"></div>
    <h2>Farms &amp; Ranches</h2>
    <p>Mauris neque metus malesuada nec ultri-cies sit amet porttitor mattis enim. In massa libero interdum nec</p>
    <a class="btn">View More</a>
  </article>
</section>

<div class="divider-soft"></div>

<section class="about">
  <h2>About Our Company</h2>
  <p class="lead">Pellentesque faucibus Ut accumsan ultricies elit Maecenas at justo id velit placerat mo-lestie Donec dictum lectus non odio Cras a ante vitae enim iaculis aliquam</p>
  <p>Duis tincidunt lectus quis dui viverra vestibulum. Suspendisse vulputate aliquam dui. Nulla elemen-tum dui ut augue. Aliquam vehicula mi at mauris. Maecenas placerat, nisl at consequat rhoncus, sem nunc gravida justo, quis eleifend arcu velit quis lacus.</p>
  <p>Aliquam nec erat at purus cursus interdum Vestibulum ligula augue bibendum accumsan vestibulum ut commodo a mi Morbi ornare gravida elit Integer congue augue et malesuada iaculis ipsum dui aliquet felis at cursus , imperdiet vitae, tellus.</p>
</section>

<aside class="gallery">
  <h3>OUR GALLERY</h3>
  <div class="thumbs">
    <div class="thumb"><div role="img" aria-label="Farmhouse in a wheat field" style="background:linear-gradient(#5aa0d8,#c9a35a 60%)"></div></div>
    <div class="thumb"><div role="img" aria-label="Office building" style="background:linear-gradient(#b9c8d6,#5d6d7d)"></div></div>
    <div class="thumb"><div role="img" aria-label="Living room interior" style="background:linear-gradient(135deg,#c7a67a,#6f5a44)"></div></div>
    <div class="thumb"><div role="img" aria-label="Terrace with sea view" style="background:linear-gradient(#8ec3e6,#3d7fa8 60%,#d0d0d0)"></div></div>
    <div class="thumb"><div role="img" aria-label="Traditional family house" style="background:linear-gradient(#cfd6dc,#8b8478 60%,#5d7a3d)"></div></div>
    <div class="thumb"><div role="img" aria-label="Suburban home with lawn" style="background:linear-gradient(#5b8ccc,#8a5a4a 55%,#4e7a35)"></div></div>
  </div>
</aside>

<footer class="footer">
  <div class="footer-stripe"></div>
  <div class="footer-col" style="left:65px"><h4>About us</h4><a>About Us</a><a>Commercial</a><a>Residential</a><a>Farms</a><a>Vacant Land</a></div>
  <div class="footer-col" style="left:176px"><h4>Featured</h4><a>Term Deposits</a><a>Management &amp; Startegy</a><a>Client Relations</a><a>Financial Privacy</a><a>Tax Advice</a></div>
  <div class="footer-col" style="left:315px"><h4>Sublinks</h4><a>Overview</a><a>Administration</a><a>Funds Security</a><a>Core Services</a><a>Reporting</a></div>
  <div class="footer-col" style="left:429px"><h4>Support</h4><a>Support</a><a>Testimonials</a><a>Contact Us</a></div>
  <div class="footer-col" style="left:540px"><h4>Get Connected</h4><div class="footer-social"><span></span><span></span><span></span><span></span></div></div>
  <div class="footer-rule"></div>
  <div class="copyright">Copyright © 2014 Company Name.&nbsp; All right reseved</div>
</footer>
</body>
</html>
```